Zelvo Stationary

Design the stationary of Zelvo Promotions Group.

Zelvo is a BTL company, BTL meaning "below the line". In other words Zelvo is a Promotional Marketing company (the company that design the brands promotional activities).

The design should transmit creativity, agility, boldness.

I need:
* Bis Card
* Letter head
* Envelopes, both vertical and horizontal (for legal size), and letter envelope
* Folders
* PPT template (Title page and regular page)
* CD slip (CD envelope)
* ID card (employee card)

And what ever else you want to throw in.
Updates

Guys,

Something I missed from the brief.   The predominat color should be RED.

Also, have fun and play with the exclamation mark (!) of the logo. 

Hi guys, more comments:

Remember that Zelvo is a "creativity" agency, not in the advertising side but on the promotional side, and that should reflect on the stationary.

 I want a bold design.  Bold and yet crisp.

 

Guys, i just uploaded the Logo in AI format.

I Also uploaded the actual Zelvo Bis Card, wich I like.  So I will like to see some designs with that bis card approach.

Guys, I am so sorry, but I notice in your last post that I upladed a wrong design ("13154_promotions_group_zelvo_brief225630.ai").  The problem was that I asked the designer the file in AI format and he send me thw wrong file, and since I dont have Illustrator I could not verify it.

The differences are minor, I just already ask him the correct one (similar to the EPS file).

Sorry                                   

Just post the correct AI file : "Zelvo Logo.ai"

Reason: I'm expecting more designs to choose from and also I wont be available tomorrow to decide.

Reason: Sorry guys, but we are not there yet!

Target Market(s)

Marketing directors, Marketing Managers

Industry/Entity Type

Legal

Requirements
Must have
• Must work with the logo attached.
The predominat color should be RED.
Play and have fun with the exclamation mark (!).
Should not have
• * No old fonts

Should not be:
* boring
* Informal
* rigid

```html
<!DOCTYPE html>
<html lang="en">
<head>
<meta charset="utf-8">
<title>Zelvo Promotions Group — Letterhead</title>
<link rel="stylesheet" href="https://fonts.googleapis.com/css2?family=Montserrat:wght@600;700&display=swap">
<style>
  :root {
    --red-deep: #4a0004;
    --red-band: #8c0a12;
    --red-text: #d01a22;
    --ink: #111111;
    --paper: #ffffff;
    --white: #ffffff;
  }
  html, body {
    margin: 0;
    padding: 0;
    width: 848px;
    height: 1200px;
    overflow: hidden;
    background: var(--paper);
  }
  .letterhead {
    position: relative;
    width: 848px;
    height: 1200px;
    background: var(--paper);
    font-family: "Montserrat", "Century Gothic", sans-serif;
  }
  .top-band {
    position: absolute;
    left: 0; top: 0;
    width: 100%;
    height: 56px;
    background:
      linear-gradient(90deg, var(--red-deep) 0%, var(--red-band) 18%, var(--red-deep) 36%, var(--red-band) 56%, var(--red-deep) 74%, var(--red-band) 86%, var(--red-deep) 100%);
  }
  .top-band::after {
    content: "";
    position: absolute;
    inset: 0;
    background: linear-gradient(180deg, rgba(255,255,255,0.06) 0%, rgba(0,0,0,0.18) 100%);
  }
  .brand {
    position: absolute;
    left: 30px;
    top: 92px;
    display: flex;
    align-items: center;
    gap: 14px;
    color: var(--ink);
    font-weight: 700;
  }
  .brand-name {
    display: flex;
    flex-direction: column;
    line-height: 1;
  }
  .brand-word {
    font-size: 50px;
    letter-spacing: -1px;
    text-transform: lowercase;
  }
  .brand-sub {
    font-size: 10.5px;
    letter-spacing: 4.2px;
    margin-top: 6px;
    text-transform: uppercase;
  }
  .brand-dot {
    width: 30px;
    height: 30px;
    border-radius: 50%;
    background: var(--red-text);
    align-self: flex-end;
    margin-bottom: 2px;
  }
  .address {
    position: absolute;
    left: 0;
    top: 1141px;
    width: 100%;
    text-align: center;
    color: var(--red-text);
    font-weight: 600;
    font-size: 11.5px;
    line-height: 15px;
  }
  .address p { margin: 0; }
  .bottom-band {
    position: absolute;
    left: 0; bottom: 0;
    width: 100%;
    height: 26px;
    background:
      linear-gradient(90deg, var(--red-deep) 0%, var(--red-band) 30%, var(--red-deep) 55%, var(--red-band) 80%, var(--red-deep) 100%);
    display: flex;
    align-items: center;
    justify-content: center;
    color: var(--white);
    font-weight: 600;
    font-size: 8.5px;
  }
  .bottom-band .web {
    font-size: 14px;
    font-weight: 600;
    margin-left: 4px;
    letter-spacing: 0.3px;
  }
</style>
</head>
<body>
  <main class="letterhead">
    <div class="top-band"></div>

    <header class="brand" aria-label="Zelvo Promotions Group">
      <div class="brand-name">
        <span class="brand-word">zelvo</span>
        <span class="brand-sub">Promotions Group</span>
      </div>
      <span class="brand-dot"></span>
    </header>

    <footer>
      <div class="address">
        <p>Calle 18 No. 42 Ens Las Palmas, Santo Domingo, Republica Dominicana</p>
        <p>Tell: 809.555.0142 | Fax: 809.555.0187</p>
      </div>
      <div class="bottom-band">
        For more information please visit our website @<span class="web">www.zelvo.com.do</span>
      </div>
    </footer>
  </main>
</body>
</html>
```